Website for Torvel Capital - investment banking firm

We have a corporate identity (thanks to Ravinka/31842) and want to extend that into a website design.  See the attached zipped files.
We have software folks in-house to do the coding.
See the attached Project Brief & Notes for more details.  Don't worry about the actual text - lorem ipsum will be fine.
The server will be Apache.
Thank you!
Desmond

Industry/Entity Type
Investment

```html
<!DOCTYPE html>
<html lang="en">
<head>
<meta charset="utf-8">
<title>Torvel Capital</title>
<link rel="stylesheet" href="https://fonts.googleapis.com/css2?family=Open+Sans:wght@400;600;700&family=Montserrat:wght@500;600&family=Arimo&display=swap">
<style>
:root{
  --navy:#1c3f86;
  --navy-deep:#102a63;
  --band-top:#0f2f6e;
  --band-bottom:#1f56a8;
  --header-bg:#efefef;
  --text:#333;
  --muted:#666;
  --red:#c8171d;
  --rule:#d6d6d6;
  --white:#fff;
}
*{margin:0;padding:0;box-sizing:border-box}
html,body{width:797px;height:1200px;overflow:hidden;background:var(--white)}
body{position:relative;font-family:"Open Sans",sans-serif;color:var(--text)}
.abs{position:absolute}

.topbar{left:0;top:0;width:797px;height:34px;background:linear-gradient(var(--navy-deep),var(--navy))}
.topbar .contact{top:10px;font-size:10px;color:var(--white);display:flex;align-items:center;gap:7px}
.search{left:542px;top:9px;width:149px;height:16px;background:var(--white);border-radius:2px;font-size:6.5px;font-style:italic;color:var(--navy);padding:4px 5px}
.search svg{position:absolute;right:5px;top:3px}

.header{left:0;top:34px;width:797px;height:61px;background:var(--header-bg)}
.logo{left:106px;top:22px;display:flex;align-items:center;gap:8px;font-size:16px;font-weight:600;color:var(--navy);letter-spacing:.5px}
.logo .mark{width:22px;height:22px;background:var(--navy)}
.nav{left:299px;top:28px;display:flex;gap:20px;font-size:10.5px;color:#777}
.nav .active{color:var(--navy)}

.hero{left:0;top:95px;width:797px;height:357px;background:radial-gradient(ellipse at 45% 50%,#3fc7ef 0%,#1a8fc9 45%,#0b4f8f 100%)}
.dots{left:374px;top:436px;display:flex;gap:6px}
.dots span{width:7.5px;height:7.5px;border-radius:50%;background:#e9f3fb}
.dots span.on{background:#1a5fae}
.hero-shadow{left:120px;top:452px;width:560px;height:30px;background:radial-gradient(ellipse at 50% 0%,rgba(0,0,0,.22),rgba(0,0,0,0) 70%)}

.section-title{font-size:17px;font-weight:700;color:var(--navy)}
.services-title{left:0;width:797px;top:483px;text-align:center}
.services{left:0;top:523px;width:797px;height:179px;background:linear-gradient(var(--band-top),var(--band-bottom))}
.service{top:0;height:179px;text-align:center;color:var(--white);font-family:"Montserrat",sans-serif}
.service+.service{border-left:1px solid rgba(255,255,255,.18)}
.service svg{position:absolute;left:50%;transform:translateX(-50%);top:30px}
.service h3{position:absolute;top:87px;width:100%;font-size:10.5px;font-weight:600;letter-spacing:.2px}
.service p{position:absolute;top:109px;left:50%;transform:translateX(-50%);width:140px;font-size:7.5px;line-height:10.5px}

.clients-title{left:106px;top:716px}
.arrows{left:375px;top:724px}
.client{left:106px;width:286px;height:57px;border-bottom:1px solid var(--rule)}
.client .thumb{position:absolute;left:0;top:0;width:38px;height:38px;background:linear-gradient(135deg,#9fc0de,#2b5a8c)}
.client p{position:absolute;left:47px;top:0;width:240px;font-family:"Arimo",sans-serif;font-size:7.5px;line-height:11px;color:var(--text)}
.client a{position:absolute;left:49px;top:32px;font-size:7.5px;font-weight:700;color:var(--red);text-decoration:none}

.team-title{left:456px;top:716px}
.team-text{left:456px;top:751px;width:236px;font-size:7.4px;line-height:15px;color:var(--text)}
.btn{width:93px;height:23px;border-radius:4px;background:linear-gradient(#1f4a95,var(--navy-deep));color:var(--white);font-size:7.5px;text-align:center;line-height:23px}

.process-title{left:106px;top:932px}
.process-img{left:106px;top:970px;width:187px;height:126px;background:linear-gradient(90deg,#a9c4cc 0%,#6f8f98 55%,#2d3438 100%)}
.process-text{left:305px;top:964px;width:388px;font-size:7.4px;line-height:15px;color:var(--text)}

.footer{left:0;top:1130px;width:797px;height:70px;background:linear-gradient(var(--navy-deep),var(--navy))}
.footer .links{left:106px;top:19px;font-family:"Arimo",sans-serif;font-size:7.5px;color:var(--white)}
.footer .copy{left:106px;top:39px;font-family:"Arimo",sans-serif;font-size:7.5px;color:var(--white)}
.social{left:629px;top:25px;display:flex;gap:6px}
.social span{width:17px;height:17px;border-radius:50%;background:#3d69b5}
</style>
</head>
<body>

<div class="abs topbar">
  <div class="abs contact" style="left:106px">
    <svg width="17" height="11" viewBox="0 0 17 11"><rect x=".5" y=".5" width="16" height="10" fill="none" stroke="#fff"/><path d="M.5 .5 8.5 6.5 16.5 .5" fill="none" stroke="#fff"/></svg>
    info@torvelcapital.com
  </div>
  <div class="abs contact" style="left:243px">
    <svg width="13" height="13" viewBox="0 0 24 24"><path fill="#fff" d="M6.6 10.8a15.1 15.1 0 0 0 6.6 6.6l2.2-2.2c.3-.3.7-.4 1-.2 1.1.4 2.3.6 3.6.6.6 0 1 .4 1 1V20c0 .6-.4 1-1 1A17 17 0 0 1 3 4c0-.6.4-1 1-1h3.5c.6 0 1 .4 1 1 0 1.3.2 2.5.6 3.6.1.3 0 .7-.2 1z"/></svg>
    +09 318 450 72 16
  </div>
  <div class="abs search">Search.........
    <svg width="10" height="10" viewBox="0 0 10 10"><circle cx="4" cy="4" r="3" fill="none" stroke="#1c3f86" stroke-width="1.3"/><path d="M6.2 6.2 9.3 9.3" stroke="#1c3f86" stroke-width="1.6"/></svg>
  </div>
</div>

<div class="abs header">
  <div class="abs logo"><span class="mark"></span>Torvel Capital</div>
  <nav class="abs nav">
    <span class="active">Home</span><span>About</span><span>Services</span><span>Current Engagements</span><span>Completed Transactions</span>
  </nav>
</div>

<div class="abs hero" role="img" aria-label="Businesswoman touching a glowing digital interface with world map and globe"></div>
<div class="abs dots"><span class="on"></span><span></span><span></span><span></span></div>
<div class="abs hero-shadow"></div>

<h2 class="abs section-title services-title">SERVICES</h2>
<section class="abs services">
  <div class="abs service" style="left:0;width:299px">
    <svg width="54" height="48" viewBox="0 0 54 48" fill="#fff">
      <circle cx="15" cy="6" r="5"/><circle cx="27" cy="5" r="5"/><circle cx="39" cy="6" r="5"/>
      <rect x="9" y="13" width="12" height="20" rx="3"/><rect x="21" y="12" width="12" height="22" rx="3"/><rect x="33" y="13" width="12" height="20" rx="3"/>
      <path d="M2 36q25 12 50 0v4q-25 12-50 0z"/>
    </svg>
    <h3>Buy-SideAcquisitions</h3>
    <p>We assist corporate clients and private equity groups to identify opportunities for</p>
  </div>
  <div class="abs service" style="left:299px;width:199px">
    <svg width="74" height="46" viewBox="0 0 74 46" fill="#fff">
      <circle cx="20" cy="12" r="9"/><circle cx="54" cy="12" r="9"/><circle cx="37" cy="16" r="10"/>
      <path d="M2 40q4-16 18-16 8 0 12 5l-6 11z"/><path d="M72 40q-4-16-18-16-8 0-12 5l6 11z"/>
      <path d="M19 46q3-18 18-18t18 18z"/>
    </svg>
    <h3>Recapitalizations</h3>
    <p>Some companies have exciting growth prospects but lack the financial base to capitalize</p>
  </div>
  <div class="abs service" style="left:498px;width:299px">
    <svg width="60" height="48" viewBox="0 0 60 48">
      <circle cx="40" cy="15" r="11" fill="none" stroke="#fff" stroke-width="6" stroke-dasharray="4 3"/>
      <circle cx="40" cy="15" r="5" fill="none" stroke="#fff" stroke-width="3"/>
      <circle cx="18" cy="34" r="10" fill="none" stroke="#fff" stroke-width="6" stroke-dasharray="4 3"/>
      <circle cx="18" cy="34" r="4.5" fill="none" stroke="#fff" stroke-width="3"/>
    </svg>
    <h3>Sell-SideTransactions</h3>
    <p>We assist the owners of private companies to select the ideal party for a transaction</p>
  </div>
</section>

<h2 class="abs section-title clients-title">OUR CLIENTS</h2>
<svg class="abs arrows" width="18" height="12" viewBox="0 0 18 12"><path d="M7 1 2 6l5 5M11 1l5 5-5 5" fill="none" stroke="#1c3f86" stroke-width="2"/></svg>

<div class="abs client" style="top:756px">
  <div class="thumb" role="img" aria-label="Businessman at a desk"></div>
  <p>Torvel Capital has a diverse array of clients ranging from multi-billion dollar strategic acquirers to large private equity funds.</p>
  <a href="#">READ MORE</a>
</div>
<div class="abs client" style="top:813px">
  <div class="thumb" role="img" aria-label="Businessman with digital screen"></div>
  <p>We will not engage a client as a buyer if we believe there is any chance of them wasting our time or a prospective seller's time.</p>
  <a href="#">READ MORE</a>
</div>
<div class="abs client" style="top:870px">
  <div class="thumb" role="img" aria-label="Businesswoman portrait" style="background:linear-gradient(135deg,#f2f2f2,#c9c9c9)"></div>
  <p>Once we have your acquisition parameters, we feed these into our software to create an initial target list. The criteria used to create this</p>
  <a href="#">READ MORE</a>
</div>

<h2 class="abs section-title team-title">OUR TEAM</h2>
<p class="abs team-text">Experienced professionalssupported by expert research team and sophisticated technology Torvel Capital's team of bankers and advisors is comprised of experienced professionals. Our research team is critical in finding deals where there is sufficient strategic overlap that will result in a deal valuation and structure that will work for both buyer and seller. Simply said, we find deals that nobody else can.</p>
<div class="abs btn" style="left:455px;top:871px">READ MORE</div>

<h2 class="abs section-title process-title">OUR PROCESS</h2>
<div class="abs process-img" role="img" aria-label="Businessman drawing a process flowchart"></div>
<p class="abs process-text">When our software has identified a qualified list, Torvel will reach out to prospective sellers. We will gather basic information during this process. At this time, we will keep all information within our firm until we have approval by the potential seller to reach out directly to the buyer. When our software has identified a qualified list, Torvel will reach out to prospective sellers. We will gather basic information during this process. At this time, we will keep all information within our firm until we have approval by the potential seller to reach out directly to the buyer. When our software has identified a qualified list, Torvel will reach</p>
<div class="abs btn" style="left:305px;top:1069px">READ MORE</div>

<footer class="abs footer">
  <div class="abs links">About Us | Resource | Expertise | References | Contact Us</div>
  <div class="abs copy">© 2014 Copyright Torvel Capital. . All Rights Reserved.</div>
  <div class="abs social"><span></span><span></span><span></span></div>
</footer>

</body>
</html>
```